Business Card Design for a Personal Trainer

I need a business card design for my job as a personal trainer. It should have a unique, modern and exclusive design. On the front there should be only my logo with my name and my job. 0162/3819204 Tobias Lendhart Wiesengrundweg 14 80417 Munich Germany The most important contact information is the web adress. it can be bigger than the rest, but its not necessary. The card should be 8,5cmx5,5cm big. Font: Roboto. Colors: black, white, gray, 56c1ff.

```html
<!DOCTYPE html>
<html lang="de">
<head>
<meta charset="utf-8">
<title>Tobias Lendhart – Personal Trainer Business Card</title>
<link rel="stylesheet" href="https://fonts.googleapis.com/css2?family=Roboto:wght@300;400;500&family=Roboto+Condensed:wght@500&display=swap">
<style>
  :root {
    --stage: #d9d5d0;
    --card: #262525;
    --ink: #ffffff;
    --ink-soft: #e6e6e6;
    --rule: #7a7a7a;
    --photo-light: #eeeeee;
    --photo-dark: #4a4a4a;
  }
  * { margin: 0; padding: 0; box-sizing: border-box; }
  html, body { width: 1200px; height: 900px; overflow: hidden; }
  body {
    position: relative;
    background: var(--stage);
    font-family: "Roboto", Arial, sans-serif;
    color: var(--ink);
  }
  .card {
    position: absolute;
    left: 330px;
    width: 558px;
    height: 344px;
    background: var(--card);
    box-shadow: 3px 4px 8px rgba(0,0,0,0.35);
  }
  .card--contact { top: 90px; }
  .card--brand { top: 470px; }

  .portrait {
    position: absolute;
    left: 38px;
    top: 58px;
    width: 225px;
    height: 230px;
    border-radius: 22px;
    background: linear-gradient(180deg, var(--photo-light) 0%, #cfcfcf 55%, var(--photo-dark) 100%);
  }
  .identity {
    position: absolute;
    left: 278px;
    top: 76px;
    width: 240px;
    text-align: center;
  }
  .identity__name {
    font-weight: 400;
    font-size: 25px;
    letter-spacing: 0.3px;
    text-transform: uppercase;
    line-height: 1;
    white-space: nowrap;
  }
  .identity__role {
    display: flex;
    align-items: center;
    gap: 6px;
    margin-top: 5px;
    font-size: 10.5px;
    letter-spacing: 2.6px;
    text-transform: uppercase;
    white-space: nowrap;
  }
  .identity__role::before,
  .identity__role::after {
    content: "";
    flex: 1;
    height: 1px;
    background: var(--ink);
  }
  .contact {
    position: absolute;
    left: 280px;
    top: 137px;
    font-size: 16px;
    line-height: 21px;
    color: var(--ink-soft);
  }
  .contact__line { display: flex; align-items: center; gap: 5px; }
  .contact__line svg { width: 15px; height: 12px; fill: var(--ink); }
  .contact__address { margin-top: 7px; }
  .divider {
    position: absolute;
    left: 282px;
    top: 240px;
    width: 234px;
    height: 1px;
    background: var(--rule);
  }
  .website {
    position: absolute;
    left: 286px;
    top: 248px;
    font-family: "Roboto Condensed", "Roboto", Arial, sans-serif;
    font-weight: 500;
    font-size: 21px;
  }

  .brand {
    position: absolute;
    left: 0;
    right: 0;
    top: 92px;
    display: flex;
    flex-direction: column;
    align-items: center;
  }
  .brand__mark {
    width: 44px;
    height: 44px;
    background: var(--ink);
    margin-bottom: 38px;
  }
  .brand__name {
    font-weight: 400;
    font-size: 32px;
    letter-spacing: 0.4px;
    text-transform: uppercase;
    line-height: 1;
    white-space: nowrap;
  }
  .brand__role {
    display: flex;
    align-items: center;
    gap: 7px;
    width: 310px;
    margin-top: 6px;
    font-size: 13px;
    letter-spacing: 3.2px;
    text-transform: uppercase;
    white-space: nowrap;
  }
  .brand__role::before,
  .brand__role::after {
    content: "";
    flex: 1;
    height: 1px;
    background: var(--ink);
  }
</style>
</head>
<body>
  <section class="card card--contact">
    <div class="portrait" role="img" aria-label="Black and white portrait photo of the trainer"></div>
    <div class="identity">
      <h1 class="identity__name">Tobias Lendhart</h1>
      <p class="identity__role">Personal Trainer</p>
    </div>
    <div class="contact">
      <p class="contact__line">
        <svg viewBox="0 0 16 12" aria-hidden="true"><path d="M2 3 Q8 -1 14 3 L13 5 L11 4.5 L10.5 3 Q8 2.3 5.5 3 L5 4.5 L3 5 Z M4 6 L12 6 L14 11 L2 11 Z"/></svg>
        0162/3819204
      </p>
      <p class="contact__line">
        <svg viewBox="0 0 16 12" aria-hidden="true"><path d="M1 1 H15 V11 H1 Z M2 2 V2.5 L8 7 L14 2.5 V2 Z" fill-rule="evenodd"/></svg>
        t.lendhart@postfeld.de
      </p>
      <p class="contact__address">Wiesengrundweg 14<br>80417 München</p>
    </div>
    <div class="divider"></div>
    <p class="website">www.tobiaslendhart.de</p>
  </section>

  <section class="card card--brand">
    <div class="brand">
      <div class="brand__mark" aria-hidden="true"></div>
      <h2 class="brand__name">Tobias Lendhart</h2>
      <p class="brand__role">Personal Trainer</p>
    </div>
  </section>
</body>
</html>
```